Landing Page Design for Adult Dating Age Verification (18+)

The objective of this task is to design a visually appealing pre-landing page for the adult dating site "Quillmera (site: https://quillmera.com/)" with an age verification mechanism. The pre-landing page will feature two buttons that redirect visitors to the main offer. The design should also include a footer block that includes links to the terms of use, privacy policy, and contact us pages.

Design Requirements:
Develop an age verification section prominently displayed on the pre-landing page.
Design the section to include two buttons labeled "Yes" and "No" for visitors to confirm their age.
Ensure the section is visually appealing and clearly communicates the purpose of age verification.

Visual Appeal:
Create a visually appealing design that aligns with the branding and theme of the "Quillmera" adult dating site.
Use suitable color schemes, typography, and graphics to enhance the overall visual appeal of the pre-landing page.

Layout and Navigation:
Design an engaging and intuitive layout that encourages visitors to interact with the page and proceed to the main offer.
Ensure clear and visible navigation elements that direct visitors to the main offer or provide additional information.

Responsive Design:
Develop a responsive design that provides a seamless user experience across various devices, including desktop and mobile.
Ensure the design elements and layout adapt well to different screen sizes and resolutions.

File Formats and Assets:
Deliver the final design in PSD, AI, or Sketch format, ensuring that the files are well-organized and layered.
Include any necessary images or assets used in the design, ensuring they are of high quality and optimized for web use.

```html
<!DOCTYPE html>
<html lang="en">
<head>
<meta charset="UTF-8">
<title>Quillmera – Age Verification</title>
<link rel="stylesheet" href="https://fonts.googleapis.com/css2?family=Abril+Fatface&family=Mulish:wght@300;400&display=swap">
<style>
  :root {
    --page-bg: #f1ece9;
    --plum: #8f5496;
    --lavender: #d4b6d9;
    --ink: #1f1d22;
    --brand-ink: #2e2b33;
    --photo-dark: #3a2720;
    --photo-mid: #6b4a3c;
    --photo-warm: #b4876f;
  }
  * { margin: 0; padding: 0; box-sizing: border-box; }
  html, body {
    width: 1200px;
    height: 640px;
    overflow: hidden;
    background: var(--page-bg);
  }
  .age-gate {
    position: relative;
    width: 1200px;
    height: 640px;
    overflow: hidden;
    background: var(--page-bg);
    font-family: 'Mulish', sans-serif;
    color: var(--ink);
  }
  .heart-art {
    position: absolute;
    inset: 0;
    width: 1200px;
    height: 640px;
  }
  .brand {
    position: absolute;
    left: 70px;
    top: 62px;
    display: flex;
    align-items: center;
    gap: 10px;
  }
  .brand-dot {
    width: 36px;
    height: 36px;
    border-radius: 50%;
    background: var(--lavender);
  }
  .brand-name {
    font-family: 'Abril Fatface', serif;
    font-size: 22px;
    color: var(--brand-ink);
    letter-spacing: 0.5px;
  }
  .gate-title {
    position: absolute;
    left: 65px;
    top: 138px;
    font-family: 'Abril Fatface', serif;
    font-weight: 400;
    font-size: 60px;
    line-height: 72px;
    color: var(--plum);
    letter-spacing: -1px;
  }
  .gate-note {
    position: absolute;
    left: 67px;
    top: 314px;
    font-weight: 300;
    font-size: 33px;
    line-height: 42px;
    color: var(--ink);
  }
  .gate-actions {
    position: absolute;
    left: 70px;
    top: 478px;
    display: flex;
    gap: 15px;
  }
  .gate-button {
    display: flex;
    align-items: center;
    justify-content: center;
    width: 124px;
    height: 48px;
    border-radius: 18px;
    background: var(--plum);
    color: #fff;
    font-family: 'Mulish', sans-serif;
    font-weight: 300;
    font-size: 26px;
    text-decoration: none;
  }
  .site-footer {
    position: absolute;
    left: 70px;
    top: 589px;
    display: flex;
    align-items: center;
    font-size: 14px;
    font-weight: 400;
    color: var(--ink);
  }
  .site-footer a { color: inherit; text-decoration: none; }
  .site-footer .sep { margin: 0 7px; }
  .site-footer .copyright { margin-left: 6px; }
</style>
</head>
<body>
<main class="age-gate">
  <svg class="heart-art" viewBox="0 0 1200 640" xmlns="http://www.w3.org/2000/svg">
    <defs>
      <linearGradient id="photoTone" x1="0" y1="0" x2="1" y2="1">
        <stop offset="0" stop-color="var(--photo-mid)"/>
        <stop offset="0.45" stop-color="var(--photo-dark)"/>
        <stop offset="0.7" stop-color="var(--photo-warm)"/>
        <stop offset="1" stop-color="var(--photo-dark)"/>
      </linearGradient>
    </defs>
    <path class="heart-frame" fill="var(--lavender)"
      d="M836,628 L530,320 C470,260 450,180 480,110 C520,10 620,-40 710,-30 C780,-22 820,20 836,100 C852,20 892,-22 962,-30 C1052,-40 1152,10 1192,110 C1222,180 1202,260 1142,320 Z"/>
    <path class="heart-photo" fill="url(#photoTone)" role="img"
      aria-label="Photo of an embracing couple in a warm, dimly lit loft bedroom"
      d="M836,560 L600,320 C555,275 535,215 548,160 C565,85 625,48 690,48 C760,48 815,80 836,104 C857,80 912,48 982,48 C1047,48 1107,85 1124,160 C1137,215 1117,275 1072,320 Z"/>
  </svg>

  <a class="brand" href="https://quillmera.com/">
    <span class="brand-dot"></span>
    <span class="brand-name">Quillmera</span>
  </a>

  <h1 class="gate-title">Are you over<br>the age of 18?</h1>

  <p class="gate-note">You must be 18 or<br>over to view content<br>on this page</p>

  <div class="gate-actions">
    <a class="gate-button" href="https://quillmera.com/">Yes</a>
    <a class="gate-button" href="#">No</a>
  </div>

  <footer class="site-footer">
    <a href="#">Terms of use</a><span class="sep">|</span>
    <a href="#">Privacy Policy</a><span class="sep">|</span>
    <a href="#">Contact us</a><span class="sep">|</span>
    <span class="copyright">Copyright © 2023 All Rights Reserved</span>
  </footer>
</main>
</body>
</html>
```